full stationary design for a modern sleek design company

we are a design company that does modern minimalistic interior design works as well as other design services for high end clients.
we need a full stationary design including and not limited to (double sided business card, letter head, envelopes, documents folder...etc) that reflects the modern style design we do.
sleek modern and minimalistic is the requirements.
Updates

please use the latest attached files as there was a slight modification on the logo Added Wednesday, March 1, 2017

minor update on the logo files in JPG and PSD has been updated kindly follow the new attachments. Added Thursday, March 2, 2017

Target Market(s)

modern minimalist clients

Industry/Entity Type

Design Agency

Requirements
Must have
• the logo
Nice to have
• i like the colors in the colored 3D logo attached
Should not have
• too many colors

```html
<!DOCTYPE html>
<html lang="en">
<head>
<meta charset="utf-8">
<title>Linear Atelier — Stationery Set</title>
<link rel="stylesheet" href="https://fonts.googleapis.com/css2?family=Montserrat:wght@400;600;700&family=Open+Sans:wght@400;700&family=Great+Vibes&display=swap">
<style>
  :root {
    --bg: #e4e6ec;
    --paper: #f7f7f7;
    --ink: #4a4a4a;
    --dark: #474747;
    --accent: #f29a1f;
    --muted: #8a8a8a;
    --line: #d3d3d3;
  }
  * { box-sizing: border-box; margin: 0; padding: 0; }
  html, body { width: 1200px; height: 907px; overflow: hidden; }
  body { background: var(--bg); font-family: "Open Sans", sans-serif; color: var(--ink); position: relative; }

  .sheet { position: absolute; background: var(--paper); overflow: hidden; }
  .sheet--dark { background: var(--dark); color: #fff; }

  .brand { display: flex; align-items: center; gap: 4px; font-family: "Montserrat", sans-serif; font-weight: 700; color: var(--ink); letter-spacing: .04em; text-transform: uppercase; white-space: nowrap; }
  .brand__square { width: 8px; height: 8px; background: var(--accent); flex: none; }
  .brand--light { color: #fff; }

  .contact { position: absolute; left: 14px; bottom: 12px; padding-left: 5px; border-left: 2px solid var(--accent); font-size: 4.2px; line-height: 1.5; color: var(--ink); }

  /* letter */
  .letter { width: 272px; padding: 24px 26px 0; }
  .letter .brand { font-size: 8px; margin-bottom: 66px; }
  .letter__intro { font-weight: 700; font-size: 5px; line-height: 1.45; margin-bottom: 8px; }
  .letter p { font-size: 4.6px; line-height: 1.55; color: #666; margin-bottom: 9px; }
  .letter--left { left: 149px; top: 27px; height: 378px; }
  .letter--center { left: 487px; top: 293px; height: 392px; }

  /* envelopes */
  .envelope-front { left: 479px; top: 92px; width: 285px; height: 139px; }
  .envelope-front .brand { position: absolute; left: 20px; top: 20px; font-size: 10px; }
  .envelope-back { left: 780px; top: 92px; width: 282px; height: 139px; }
  .envelope-back svg { position: absolute; inset: 0; }
  .envelope-back .brand { position: absolute; left: 50%; top: 14px; transform: translateX(-50%); font-size: 6px; }

  /* folder */
  .folder { left: 149px; top: 479px; width: 272px; height: 381px; }
  .folder .brand { position: absolute; left: 50%; top: 150px; transform: translateX(-50%); font-size: 17px; gap: 8px; }
  .folder .brand__square { width: 14px; height: 14px; }
  .folder__web { position: absolute; left: 0; right: 0; bottom: 22px; text-align: center; font-size: 6px; color: #ddd; }

  /* cd */
  .cd-cover { left: 816px; top: 298px; width: 162px; height: 162px; }
  .cd-cover .brand { position: absolute; left: 50%; top: 72px; transform: translateX(-50%); font-size: 10px; }
  .cd { position: absolute; left: 816px; top: 493px; width: 160px; height: 160px; }
  .cd__label { font-size: 4.5px; fill: var(--muted); font-family: "Open Sans", sans-serif; }
  .cd__brand { font-family: "Montserrat", sans-serif; font-weight: 700; font-size: 6px; fill: var(--ink); letter-spacing: .04em; }

  /* compliments slip */
  .slip { left: 491px; top: 725px; width: 268px; height: 128px; }
  .slip .brand { position: absolute; left: 18px; top: 18px; font-size: 10px; }
  .slip__script { position: absolute; right: 16px; bottom: 10px; font-family: "Great Vibes", cursive; font-size: 15px; color: var(--ink); }

  /* business cards */
  .card-back { left: 819px; top: 677px; width: 118px; height: 67px; }
  .card-back .brand { position: absolute; left: 50%; top: 28px; transform: translateX(-50%); font-size: 6px; gap: 3px; }
  .card-back .brand__square { width: 5px; height: 5px; }
  .card-front { left: 819px; top: 767px; width: 118px; height: 74px; }
  .card-front .brand { position: absolute; left: 9px; top: 18px; font-size: 5.5px; gap: 3px; }
  .card-front .brand__square { width: 5px; height: 5px; }
  .card-front__person { position: absolute; left: 9px; top: 38px; font-size: 3.6px; line-height: 1.5; }
  .card-front__name { font-weight: 700; color: var(--accent); }
  .card-front__details { position: absolute; left: 60px; top: 38px; font-size: 3.2px; line-height: 1.5; color: var(--muted); }
</style>
</head>
<body>

  <article class="sheet letter letter--left">
    <div class="brand"><span class="brand__square"></span>Linear Atelier</div>
    <p class="letter__intro">Thank you for choosing our studio. This letter sets out the scope, schedule and fees for your new residence project.</p>
    <p>Our team will begin with a site visit and a short survey of each room. We will then share mood boards, material samples and a first layout plan for your review within two weeks.</p>
    <p>Once the layout is approved, we prepare detailed drawings, lighting plans and a furniture schedule. Each stage is followed by a meeting so that every choice is clear and agreed.</p>
    <p>Fees are billed in three parts: at signing, at design approval and at final handover. All sourcing is handled by our studio at trade prices.</p>
    <p>We look forward to working with you.</p>
    <div class="contact">000 - 1234 - 5678<br>hello@linearatelier.com<br>www.linearatelier.com</div>
  </article>

  <section class="sheet envelope-front">
    <div class="brand"><span class="brand__square"></span>Linear Atelier</div>
    <div class="contact">000 - 1234 - 5678<br>hello@linearatelier.com<br>www.linearatelier.com</div>
  </section>

  <section class="sheet envelope-back">
    <svg width="282" height="139" viewBox="0 0 282 139" aria-hidden="true">
      <polygon points="0,0 282,0 282,8 141,44 0,8" fill="var(--dark)"/>
    </svg>
    <div class="brand brand--light"><span class="brand__square" style="width:5px;height:5px"></span>Linear Atelier</div>
  </section>

  <section class="sheet sheet--dark cd-cover">
    <div class="brand brand--light"><span class="brand__square"></span>Linear Atelier</div>
  </section>

  <article class="sheet letter letter--center">
    <div class="brand"><span class="brand__square"></span>Linear Atelier</div>
    <p class="letter__intro">Thank you for choosing our studio. This letter sets out the scope, schedule and fees for your new residence project.</p>
    <p>Our team will begin with a site visit and a short survey of each room. We will then share mood boards, material samples and a first layout plan for your review within two weeks.</p>
    <p>Once the layout is approved, we prepare detailed drawings, lighting plans and a furniture schedule. Each stage is followed by a meeting so that every choice is clear and agreed.</p>
    <p>Fees are billed in three parts: at signing, at design approval and at final handover. All sourcing is handled by our studio at trade prices.</p>
    <p>We look forward to working with you.</p>
    <div class="contact">000 - 1234 - 5678<br>hello@linearatelier.com<br>www.linearatelier.com</div>
  </article>

  <svg class="cd" viewBox="0 0 160 160" aria-label="Disc label">
    <circle cx="80" cy="80" r="79" fill="var(--paper)" stroke="var(--line)" stroke-width="1"/>
    <circle cx="80" cy="80" r="22" fill="none" stroke="var(--line)" stroke-width="1"/>
    <circle cx="80" cy="80" r="10" fill="var(--bg)" stroke="var(--line)" stroke-width="1"/>
    <text class="cd__label" x="40" y="27">Project:</text>
    <line x1="60" y1="27" x2="118" y2="27" stroke="var(--line)" stroke-width=".6"/>
    <text class="cd__label" x="45" y="41">Date:</text>
    <line x1="60" y1="41" x2="112" y2="41" stroke="var(--line)" stroke-width=".6"/>
    <rect x="58" y="127" width="5" height="5" fill="var(--accent)"/>
    <text class="cd__brand" x="66" y="132">LINEAR ATELIER</text>
  </svg>

  <section class="sheet sheet--dark folder">
    <div class="brand brand--light"><span class="brand__square"></span>Linear Atelier</div>
    <div class="folder__web">www.linearatelier.com</div>
  </section>

  <section class="sheet slip">
    <div class="brand"><span class="brand__square"></span>Linear Atelier</div>
    <div class="slip__script">With Compliments</div>
  </section>

  <section class="sheet sheet--dark card-back">
    <div class="brand brand--light"><span class="brand__square"></span>Linear Atelier</div>
  </section>

  <section class="sheet card-front">
    <div class="brand"><span class="brand__square"></span>Linear Atelier</div>
    <div class="card-front__person"><span class="card-front__name">NOAH VERLAINE</span><br>Creative Director</div>
    <div class="card-front__details">12 Harbour Lane, Suite 4<br>000 - 1234 - 5678<br>hello@linearatelier.com</div>
  </section>

</body>
</html>
```